Website Home Page Main Banner Design (wholesale)

1170 x 547 PNG web banner design

Varnel Global Corporation is a full-service importer based out of New York City, New York. For over 50 years, we have offered our customers fashionable, quality products at competitive prices. The company has a full in-house development and design staff, with a 100,000 sq. foot warehouse in Perth Amboy, New Jersey. Our talented design team, with extensive overseas sourcing experience, is always on the search for innovative ideas and hot new products.

Varnel currently consists of the following divisions– Toddler Novelty Company (TNC), Hair Accessories, Jewelry (Gleamor), General Merchandise (Brandolux), Beauty Implements, Socks & Hosiery and Electronics.

Website- https://varnel.quorblend.example/index.php/

Target Market(s)

Retailers

Industry/Entity Type

Wholesale

Number of Pages Required

1 page

Font styles to use
Serif

Colors

Designer to choose colors to be used in the design.

Requirements
Must have
• Company Name- Varnel Global Corp
Nice to have
• Some of the products featured on the site
Should not have
• Nothing

```html
<!DOCTYPE html>
<html lang="en">
<head>
<meta charset="utf-8">
<title>Varnel Global Corp — Wholesale Fashion Accessories</title>
<link rel="stylesheet" href="https://fonts.googleapis.com/css2?family=Dancing+Script:wght@700&family=Lato:wght@300;400&family=Open+Sans:wght@400&display=swap">
<style>
  :root {
    --paper-light: #f7f7f6;
    --paper-mid: #ebebea;
    --brand-lavender: #b7aef0;
    --ink-black: #111111;
    --ink-grey: #555555;
    --nav-pink: #ef8cc4;
    --nav-divider: #9a9a9a;
    --nav-rule: #cfcfcf;
  }
  * { margin: 0; padding: 0; box-sizing: border-box; }
  html, body { width: 1200px; height: 561px; overflow: hidden; }
  body { font-family: "Lato", "Helvetica Neue", Arial, sans-serif; }

  .banner {
    position: relative;
    width: 1200px;
    height: 561px;
    overflow: hidden;
  }
  .banner__paper {
    position: absolute;
    inset: 0;
    background: radial-gradient(ellipse at 50% 45%, var(--paper-light) 0%, var(--paper-mid) 100%);
  }

  .brand {
    position: absolute;
    left: 0; right: 0;
    top: 74px;
    display: flex;
    justify-content: center;
    align-items: center;
    gap: 12px;
  }
  .brand__mark {
    width: 18px; height: 18px;
    background: var(--brand-lavender);
  }
  .brand__name {
    font-family: "Lato", sans-serif;
    font-weight: 400;
    font-size: 46px;
    letter-spacing: 2px;
    color: var(--brand-lavender);
    line-height: 1;
  }
  .founded {
    position: absolute;
    left: 0; right: 0;
    top: 177px;
    text-align: center;
    font-family: "Open Sans", sans-serif;
    font-size: 15px;
    color: var(--ink-black);
    letter-spacing: 0.3px;
  }

  .tagline {
    position: absolute;
    left: 500px;
    top: 230px;
    width: 200px;
    display: flex;
    flex-direction: column;
    align-items: center;
    font-weight: 400;
    white-space: nowrap;
    text-align: center;
  }
  .tagline > span { display: block; white-space: nowrap; }
  .tagline__ruled {
    display: flex !important;
    align-items: center;
    gap: 12px;
    width: 186px;
    height: 24px;
    font-size: 17px;
    line-height: 24px;
    color: var(--ink-black);
  }
  .tagline__ruled::before,
  .tagline__ruled::after {
    content: "";
    flex: 1;
    height: 1px;
    background: var(--ink-black);
  }
  .tagline__one-stop {
    height: 28px;
    font-size: 23px;
    line-height: 28px;
    font-weight: 300;
    color: var(--ink-grey);
  }
  .tagline__script {
    height: 40px;
    font-family: "Dancing Script", cursive;
    font-weight: 700;
    font-size: 40px;
    line-height: 40px;
    color: var(--ink-black);
  }
  .tagline__ruled--in { font-size: 16px; }
  .tagline__fashion {
    height: 36px;
    font-size: 30px;
    line-height: 36px;
    font-weight: 300;
    color: var(--ink-black);
  }
  .tagline__industry {
    height: 26px;
    font-size: 17.5px;
    line-height: 26px;
    font-weight: 400;
    color: var(--ink-grey);
  }

  .divisions {
    position: absolute;
    left: 67px;
    top: 464px;
    width: 1066px;
    height: 34px;
    border-top: 1px solid var(--nav-rule);
    border-bottom: 1px solid var(--nav-rule);
    display: flex;
    justify-content: center;
    align-items: center;
    list-style: none;
    font-size: 16px;
    text-transform: uppercase;
    white-space: nowrap;
  }
  .divisions__item { color: var(--nav-pink); }
  .divisions__item + .divisions__item::before {
    content: "|";
    color: var(--nav-divider);
    margin: 0 17px;
  }
</style>
</head>
<body>
  <main class="banner">
    <div class="banner__paper" role="img" aria-label="Crumpled white paper texture background"></div>

    <header class="brand">
      <span class="brand__mark"></span>
      <span class="brand__name">Varnel</span>
    </header>
    <p class="founded">FOUNDED IN 1961</p>

    <h1 class="tagline">
      <span class="tagline__ruled">THE</span>
      <span class="tagline__one-stop">ONE-STOP-SHOP</span>
      <span class="tagline__script">for Retailers</span>
      <span class="tagline__ruled tagline__ruled--in">IN</span>
      <span class="tagline__fashion">THE FASHION</span>
      <span class="tagline__industry">ACCESSORY INDUSTRY</span>
    </h1>

    <ul class="divisions">
      <li class="divisions__item">Infant Specialty</li>
      <li class="divisions__item">Hair Accessories</li>
      <li class="divisions__item">Jewelry</li>
      <li class="divisions__item">Socks</li>
      <li class="divisions__item">HBA</li>
      <li class="divisions__item">General Merchandise</li>
    </ul>
  </main>
</body>
</html>
```